Used Semi Truck Website Redesign

We are redoing the website backend and would like to also do a front end redesign. I would like a Mobile and Desktop mockup for each page. The website has more mobile visitors than desktop visitors. Our competitor is http://www.haulwaybazaar.example. We don't want to copy them exactly but we want a site that looks more like that. We need the functionality of that site. One big difference is that we also sell parts and trailers.

We need a redesign for front page, product detail page, search result page, content page. It is very important that the site is very easy to use on mobile devices. Our target audience is Truck drivers.

Feel free to use demo fonts stock images, and icons. We will purchase necessary 3rd party media when a winner is chosen.

Target Market(s)

People who want to buy used trucks.

Coding

Coded - Design and coding required

Number of Pages Required

5+ page

Requirements
Must have
• Mockup for Desktop and Mobile pages.

```html
<!DOCTYPE html>
<html lang="en">
<head>
<meta charset="utf-8">
<title>Terms &amp; Condition</title>
<link href="https://fonts.googleapis.com/css2?family=Roboto:wght@300;400;500&display=swap" rel="stylesheet">
<style>
:root{
  --blue:#033199;
  --blue-deep:#022877;
  --orange:#f7941d;
  --ink:#111;
  --body:#555;
  --white:#fff;
  --sky:#1da1f2;
}
*{margin:0;padding:0;box-sizing:border-box}
html,body{width:988px;height:1200px;overflow:hidden}
body{font-family:'Roboto',sans-serif;background:var(--white);position:relative;color:var(--body)}
.topbar{position:absolute;top:0;left:0;width:988px;height:29px;background:var(--blue);color:var(--white);font-size:11px;display:flex;align-items:center;justify-content:space-between;padding:0 74px 0 73px}
.topbar .links span{margin:0 3px}
.header{position:absolute;top:29px;left:0;width:988px;height:48px;display:flex;align-items:center;justify-content:space-between;padding:0 74px}
.brand{font-size:22px;font-weight:300;color:#333}
.nav{display:flex;align-items:center;font-size:12px;color:#333}
.nav a{color:#333;text-decoration:none;margin-left:14px}
.social{display:flex;margin-left:18px;gap:4px}
.social span{width:20px;height:20px;border-radius:50%;display:block}
.banner{position:absolute;top:77px;left:0;width:988px;height:77px;background:var(--blue);color:var(--white);display:flex;align-items:center;justify-content:space-between;padding:0 74px}
.banner h1{font-size:19px;font-weight:300}
.crumbs{font-size:12px}
.content{position:absolute;top:202px;left:68px;width:844px}
.content h2{font-size:14.5px;font-weight:400;color:var(--ink);margin-bottom:6px}
.content p{font-size:10.3px;line-height:16px;text-align:justify}
.content .notice{font-size:11px;color:var(--ink);margin:6px 0 18px}
.content .loose{line-height:16.8px}
.content .wide{line-height:18.2px}
.sec2{margin-top:22px}
.sec3{margin-top:20px}
.footer{position:absolute;top:934px;left:0;width:988px;height:228px;background:var(--blue);color:var(--white)}
.footer h3{font-size:14.5px;font-weight:400;position:absolute}
.post{position:absolute;left:98px;width:250px;display:flex;gap:9px}
.thumb{width:51px;height:48px;background:linear-gradient(#9fb4c8,#6b6f73);flex:none}
.post b,.tweet b{font-size:11px;font-weight:400;display:block}
.date{font-size:9px;color:var(--orange);margin:2px 0}
.post p,.tweet p{font-size:9.2px;line-height:11.5px;font-weight:500}
.tweet{position:absolute;left:382px;width:230px}
.tweet .row{display:flex;gap:9px}
.tbox{width:39px;height:36px;background:var(--sky);flex:none}
.actions{font-size:10.5px;margin-top:6px}
.actions span{margin-right:12px}
.actions .on{color:var(--orange)}
.quick{position:absolute;left:721px;top:997px;display:grid;grid-template-columns:100px 100px;row-gap:6.5px;font-size:9.5px;line-height:11px;font-weight:500;color:var(--white)}
.copy{position:absolute;top:1162px;left:0;width:988px;height:38px;background:var(--blue-deep);color:var(--white);font-size:10.5px;display:flex;align-items:center;justify-content:center}
</style>
</head>
<body>
<div class="topbar">
  <div>256, 140 Trucks and trailers For Sale</div>
  <div class="links">My Trader: &nbsp; Login <span>|</span> Register <span>|</span> Find aDealer <span>|</span> Dealer Login</div>
</div>
<header class="header">
  <div class="brand">Logo Here</div>
  <nav class="nav">
    <a href="#">Find</a><a href="#">Sell</a><a href="#">Research</a>
    <div class="social">
      <span style="background:#3b5998"></span>
      <span style="background:#1da1f2"></span>
      <span style="background:#dd3333"></span>
      <span style="background:#0e4a8a"></span>
    </div>
  </nav>
</header>
<section class="banner">
  <h1>Terms &nbsp;&amp;&nbsp; Condition</h1>
  <div class="crumbs">Home &nbsp;|&nbsp; Terms &amp; Condition</div>
</section>
<main class="content">
  <h2>1. Contractual Relationship</h2>
  <p>Lorem ipsum dolor sit amet, consectetuer adipiscing elit. Aenean commodo ligula eget dolor. Aenean massa. Cum sociis natoque penatibus et magnis dis parturient montes, nascetur ridiculus mus. Donec quam felis, ultricies nec, pellentesque eu, pretium quis, sem. Nulla consequat massa quis enim. Donec pede justo, fringilla vel, aliquet nec, vulputate eget, arcu. In enim justo, rhoncus ut, imperdiet a, venenatis vitae, justo. Nullam dictum felis eu pede mollis pretium. Integer tincidunt. Cras dapibus. Vivamus elementum semper nisi. Aenean vulputate eleifend tellus. Aenean leo ligula, porttitor eu, consequat vitae, eleifend ac, enim. Aliquam lorem ante, dapibus in, viverra quis, feugiat a, tellus. Phasellus viverra nulla ut metus varius laoreet. Quisque rutrum. Aenean imperdiet. Etiam ultricies nisi vel augue. Curabitur ullamcorper ultricies nisi. Nam eget dui. Etiam rhoncus.</p>
  <p class="notice">PLEASE READ THESE TERMS CAREFULLY BEFORE ACCESSING OR USING THE SERVICES.</p>
  <p class="loose">Lorem ipsum dolor sit amet, consectetuer adipiscing elit. Aenean commodo ligula eget dolor. Aenean massa. Cum sociis natoque penatibus et magnis dis parturient montes, nascetur ridiculus mus. Donec quam felis, ultricies nec, pellentesque eu, pretium quis, sem. Nulla consequat massa quis enim. Donec pede justo, fringilla vel, aliquet nec, vulputate eget, arcu. In enim justo, rhoncus ut, imperdiet a, venenatis vitae, justo. Nullam dictum felis eu pede mollis pretium. Integer tincidunt. Cras dapibus. Vivamus elementum semper nisi. Aenean vulputate eleifend tellus. Aenean leo ligula, porttitor eu, consequat vitae, eleifend ac, enim. Aliquam lorem ante, dapibus in, viverra quis, feugiat a, tellus. Phasellus viverra nulla ut metus varius laoreet. Quisque rutrum. Aenean imperdiet. Etiam ultricies nisi vel augue. Curabitur ullamcorper ultricies nisi. Nam eget dui. Etiam rhoncus. Maecenas tempus, tellus eget condimentum rhoncus, sem quam semper libero, sit amet adipiscing sem neque sed ipsum. Nam quam nunc, blandit vel, luctus pulvinar, hendrerit id, lorem. Maecenas nec odio et ante tincidunt tempus. Donec vitae sapien ut libero venenatis faucibus. Nullam quis ante. Etiam sit amet orci eget eros faucibus tincidunt. Duis leo. Sed fringilla mauris sit amet nibh. Donec sodales sagittis magna. Sed consequat, leo eget bibendum sodales, augue velit cursus nunc,</p>

  <h2 class="sec2">2. The Services</h2>
  <p class="wide">Aenean commodo ligula eget dolor. Aenean massa. Cum sociis natoque penatibus et magnis dis parturient montes, nascetur ridiculus mus. Donec quam felis, ultricies nec, pellentesque eu, pretium quis, sem. Nulla consequat massa quis enim. Donec pede justo, fringilla vel, aliquet nec, vulputate eget, arcu. In enim justo, rhoncus ut, imperdiet a, venenatis vitae, justo. Nullam dictum felis eu pede mollis pretium. Integer tincidunt. Cras dapibus. Vivamus elementum semper nisi. Aenean vulputate eleifend tellus. Aenean leo ligula, porttitor eu, consequat vitae, eleifend ac, enim. Aliquam lorem ante, dapibus in, viverra quis, feugiat a, tellus. Phasellus viverra nulla ut metus varius laoreet. Quisque rutrum. Aenean imperdiet. Etiam ultricies nisi vel augue. Curabitur ullamcorper ultricies nisi. Nam eget dui. Etiam rhoncus. Maecenas tempus, tellus eget condimentum rhoncus, sem quam semper libero, sit amet adipiscing sem neque sed ipsum. Nam quam nunc, blandit vel, luctus pulvinar, hendrerit id, lorem. Maecenas nec odio et ante tincidunt tempus. Donec vitae sapien ut libero venenatis faucibus. Nullam quis ante. Etiam sit amet orci eget eros faucibus tincidunt. Duis leo. Sed fringilla mauris sit amet nibh. Donec sodales sagittis magna. Sed consequat, leo eget bibendum sodales, augue velit cursus nunc,.</p>

  <h2 class="sec3">3. Your Use of the Services</h2>
  <p class="wide">Aenean massa cum sociis natoque penatibus et magnis dis parturient montes, nascetur ridiculus mus. Donec quam felis, ultricies nec, pellentesque eu, pretium quis, sem. Nulla consequat massa quis enim. Donec pede justo, fringilla vel, aliquet nec, vulputate eget, arcu. In enim justo, rhoncus ut, imperdiet a, venenatis vitae, justo. Nullam dictum felis eu pede mollis pretium. Integer tincidunt. Cras dapibus. Vivamus elementum semper nisi. Aenean vulputate eleifend tellus. Aenean leo ligula, porttitor eu, consequat vitae, eleifend ac, enim. Aliquam lorem ante, dapibus in, viverra quis, feugiat a, tellus. Phasellus viverra nulla ut metus varius laoreet. Quisque rutrum. Aenean imperdiet. Etiam ultricies nisi vel augue. Curabitur ullamcorper ultricies nisi. Nam eget dui. Etiam rhoncus. Maecenas tempus, tellus eget condimentum rhoncus, sem quam semper libero, sit amet adipiscing sem neque sed ipsum. Nam quam nunc, blandit vel, luctus pulvinar, hendrerit id, lorem. Maecenas nec odio et ante tincidunt tempus. Donec vitae sapien ut libero venenatis faucibus. Nullam quis ante. Etiam sit amet orci eget eros faucibus tincidunt. Duis leo. Sed fringilla mauris sit amet nibh. Donec sodales sagittis magna. Sed consequat, leo eget bibendum sodales, augue velit cursus nunc,.Donec pede justo, fringilla vel, aliquet nec, vulputate eget, arcu. In enim justo, rhoncus ut, imperdiet a, venenatis vitae, justo. Nullam dictum felis eu pede mollis pretium. Integer tincidunt. Cras dapibus. Vivamus elementum semper nisi. Aenean vulputate eleifend tellus. Aenean leo ligula, porttitor eu, consequat vitae, eleifend ac, enim. Aliquam lorem ante, dapibus in, viverra quis, feugiat a, tellus. Phasellus viverra nulla ut metus varius laoreet. Quisque rutrum.</p>
</main>

<footer class="footer">
  <h3 style="left:98px;top:36px">Commercial Truck Blog</h3>
  <div class="post" style="top:63px">
    <div class="thumb" role="img" aria-label="Photo of a semi truck with trailer"></div>
    <div><b>Lorem ipsum dolor sit amet.</b><div class="date">&#9638; 24th November</div><p>Lorem ipsum dolor sit amet, consectetur adipiscing elit, sed do eiusmod.</p></div>
  </div>
  <div class="post" style="top:140px">
    <div class="thumb" role="img" aria-label="Photo of a blue truck cab" style="background:linear-gradient(#8fa3c9,#2d3f8f)"></div>
    <div><b>Lorem ipsum dolor sit amet.</b><div class="date">&#9638; 24th November</div><p>Lorem ipsum dolor sit amet, consectetur adipiscing elit, sed do eiusmod.</p></div>
  </div>

  <h3 style="left:382px;top:36px">Social Feed</h3>
  <div class="tweet" style="top:63px">
    <div class="row"><div class="tbox"></div><div><b>Lorem ipsum dolor sit amet.</b><p style="margin-top:2px">Lorem ipsum dolor sit amet, consectetur adipiscing elit, sed do eiusmod.</p></div></div>
    <div class="actions"><span>&#8645; Repost</span><span>&#9733; Favorite</span></div>
  </div>
  <div class="tweet" style="top:140px">
    <div class="row"><div class="tbox"></div><div><b>Lorem ipsum dolor sit amet.</b><p style="margin-top:2px">Lorem ipsum dolor sit amet, consectetur adipiscing elit, sed do eiusmod.</p></div></div>
    <div class="actions"><span>&#8645; Repost</span><span class="on">&#9733; Favorite</span></div>
  </div>

  <h3 style="left:721px;top:39px">Quick Links</h3>
</footer>
<div class="quick">
  <span>Insurance</span><span>Truck Parts</span>
  <span>Jobs &amp; Training</span><span>Steel Buildings</span>
  <span>Vehicle History</span><span>Fuel Management</span>
  <span>Truck Bodies</span><span>Shipping &amp; Transport</span>
  <span>Finance/Lease</span>
</div>
<div class="copy">Copyright 2016 &nbsp;All Rights Reserved</div>
</body>
</html>
```